Web page for a garment manufacturing company

We are clothing manufacturer based in Romania.
With our recent expansion, we have significantly increased our internal capacity, allowing us to take on new partnerships and deliver high-quality production services.
Our expertise includes producing classic coats, blazers, trousers, skirts, dresses, and blouses, though we are flexible and open to working with various other textile products.

Target Market(s)

High-end market and luxury

Industry/Entity Type

Garments Manufacturer

Coding

Coded - Design and coding required

Number of Pages Required

1 page

Colors

Designer to choose only greyscale colors for use in the design.

Requirements
Must have
• Velmora logo from our presentation
Nice to have
• https://www.lorvani.pt/
Should not have
• prices, wedding dresses, collections

```html
<!DOCTYPE html>
<html lang="en">
<head>
<meta charset="utf-8">
<title>Velmora — Garment Manufacturing</title>
<link href="https://fonts.googleapis.com/css2?family=Poppins:wght@400;500;600;700;800&family=Open+Sans:wght@400;600&display=swap" rel="stylesheet">
<style>
:root{
  --accent:#2a2a2a;
  --accent-dark:#151515;
  --eyebrow:#6e6e6e;
  --heading:#1c1c1c;
  --ink:#1a1a1a;
  --text:#5a5a5a;
  --light:#efefef;
  --footer:#0d0d0d;
  --white:#ffffff;
}
*{box-sizing:border-box;margin:0;padding:0}
html,body{width:1200px;height:3372px;overflow:hidden}
body{font-family:"Open Sans",Arial,sans-serif;color:var(--text);background:var(--white);position:relative}
h1,h2,h3,h4,.btn,.nav,.eyebrow,.brand{font-family:"Poppins",Arial,sans-serif}
.btn{display:inline-block;background:var(--accent);color:var(--white);font-size:15px;font-weight:600;padding:11px 28px;border-radius:24px;text-decoration:none}
.eyebrow{color:var(--eyebrow);font-weight:700;font-size:19px;letter-spacing:.5px;text-transform:uppercase}

/* header */
.site-header{position:absolute;top:0;left:0;width:1200px;height:120px;display:flex;align-items:center;padding:0 96px}
.brand{font-weight:800;font-size:40px;color:var(--ink);letter-spacing:1px}
.header-right{margin-left:auto;display:flex;flex-direction:column;align-items:flex-end;gap:10px}
.header-top{display:flex;align-items:center;gap:26px}
.call{display:flex;align-items:center;gap:10px}
.call-icon{width:34px;height:34px;border-radius:50%;background:var(--accent);display:flex;align-items:center;justify-content:center}
.call small{display:block;font-size:11px;color:var(--text)}
.call strong{font-family:"Poppins",sans-serif;font-size:18px;color:var(--ink);font-weight:700}
.header-top .btn{padding:9px 26px;font-size:14px}
.nav{display:flex;gap:52px;font-size:14px;font-weight:600;color:var(--ink)}
.nav a{color:inherit;text-decoration:none;padding-bottom:6px}
.nav a.active{color:var(--eyebrow);border-bottom:2px solid var(--accent)}

/* hero */
.hero{position:absolute;top:120px;left:0;width:1200px;height:700px;overflow:hidden}
.hero-photo{position:absolute;inset:0;background:linear-gradient(180deg,#e4e4e4 0%,#f0f0f0 45%,#9a9a9a 62%,#7c7c7c 80%,#999 100%)}
.hero-copy{position:absolute;top:155px;left:0;width:100%;text-align:center}
.hero-copy h1{color:var(--heading);font-size:58px;line-height:66px;font-weight:700;margin:10px 0 22px}
.hero-curve{position:absolute;bottom:0;left:0}

/* about */
.about{position:absolute;top:870px;left:0;width:1200px;height:470px}
.about-photo{position:absolute;left:98px;top:0;width:506px;height:460px;border-radius:26px;background:linear-gradient(135deg,#777,#d0d0d0 55%,#8e8e8e)}
.about-copy{position:absolute;left:670px;top:68px;width:440px}
.about-copy h2{font-size:48px;color:var(--ink);font-weight:800;margin:4px 0 20px}
.about-copy p{font-size:15px;line-height:27px;margin-bottom:26px}

/* benefits */
.benefits{position:absolute;top:1430px;left:0;width:1200px;height:550px;background:linear-gradient(180deg,var(--accent),var(--accent-dark));text-align:center;color:var(--white)}
.benefits .eyebrow{color:#c8c8c8;display:block;margin-top:48px}
.benefits h2{font-size:46px;font-weight:800;margin-top:4px}
.cards{position:absolute;top:172px;left:98px;display:flex;gap:14px}
.card{width:240px}
.card-photo{height:240px;border-radius:18px}
.card h4{font-size:13px;font-weight:600;line-height:19px;margin-top:22px;text-transform:uppercase}
.arrow{position:absolute;top:274px;width:44px;height:44px;border-radius:50%;background:rgba(255,255,255,.3);display:flex;align-items:center;justify-content:center}

/* community */
.community{position:absolute;top:2020px;left:0;width:1200px;text-align:center}
.community h2{font-size:46px;color:var(--ink);font-weight:800;margin:8px 0 22px}
.community p{width:940px;margin:0 auto 30px;font-size:15px;line-height:24px}
.media{position:absolute;top:330px;left:98px;display:flex;gap:16px}
.media-left{width:352px;height:370px;border-radius:16px;background:linear-gradient(160deg,#3c3c3c,#9a9a9a 55%,#555)}
.media-right{width:636px;height:370px;border-radius:16px;background:linear-gradient(170deg,#a8a8a8,#666 45%,#444);position:relative}
.play{position:absolute;left:50%;top:50%;transform:translate(-50%,-50%)}

/* newsletter */
.newsletter{position:absolute;top:2810px;left:0;width:1200px;height:290px;background:var(--light);text-align:center}
.newsletter h2{font-size:46px;color:var(--ink);font-weight:800;margin-top:56px}
.newsletter p{font-size:15px;margin:8px 0 26px}
.signup{display:flex;justify-content:center;gap:12px}
.signup .field{width:270px;height:42px;border-radius:21px;background:var(--white);border:1px solid #dcdcdc;text-align:left;padding:0 18px;font-size:13px;line-height:40px;color:#9a9a9a}
.signup .btn{height:42px;padding:11px 34px}

/* footer */
.site-footer{position:absolute;top:3100px;left:0;width:1200px;height:272px;background:var(--footer);color:#cfcfcf;display:flex;padding:74px 96px 0}
.site-footer h3{font-size:19px;font-weight:700;color:var(--white);margin-bottom:14px}
.site-footer p,.site-footer li{font-size:13px;line-height:21px;list-style:none}
.f-about{width:348px;padding-right:30px}
.f-links{width:208px}
.f-contact{width:260px}
.socials{display:flex;gap:10px;margin-top:16px}
.socials span{width:30px;height:30px;border-radius:50%;background:#5a5a5a}
</style>
</head>
<body>

<header class="site-header">
  <div class="brand">VELMORA</div>
  <div class="header-right">
    <div class="header-top">
      <div class="call">
        <span class="call-icon"><svg width="16" height="16" viewBox="0 0 24 24"><path fill="#fff" d="M6.6 10.8a15.2 15.2 0 006.6 6.6l2.2-2.2c.3-.3.7-.4 1-.2 1.1.4 2.3.6 3.6.6.6 0 1 .4 1 1V20c0 .6-.4 1-1 1A17 17 0 013 4c0-.6.4-1 1-1h3.5c.6 0 1 .4 1 1 0 1.3.2 2.5.6 3.6.1.3 0 .7-.2 1z"/></svg></span>
        <div><small>CALL US</small><strong>+1 555 014 2290</strong></div>
      </div>
      <a class="btn" href="#">Get Started</a>
    </div>
    <nav class="nav">
      <a class="active" href="#">HOME</a><a href="#">ABOUT US</a><a href="#">MISSION &amp; VISION</a><a href="#">OUR VALUES</a><a href="#">BENEFITS</a>
    </nav>
  </div>
</header>

<section class="hero">
  <div class="hero-photo" role="img" aria-label="Brick factory building under a clear sky"></div>
  <div class="hero-copy">
    <div class="eyebrow">Tailored for tomorrow</div>
    <h1>INNOVATING THREADS FOR<br>EVERY JOURNEY</h1>
    <a class="btn" href="#">Get Started</a>
  </div>
  <svg class="hero-curve" width="1200" height="160" viewBox="0 0 1200 160">
    <path d="M0 40 Q600 170 1200 40 L1200 160 L0 160Z" fill="#2a2a2a"/>
    <path d="M0 85 Q600 200 1200 85 L1200 160 L0 160Z" fill="#ffffff"/>
  </svg>
</section>

<section class="about">
  <div class="about-photo" role="img" aria-label="Office team working at computer desks"></div>
  <div class="about-copy">
    <div class="eyebrow">About us</div>
    <h2>WHO WE ARE</h2>
    <p>VELMORA is a manufacturing company for Ready-to-wear, situated in Oradea, a city with a rich tradition in the clothing industry. The top management is international, and we are proud to have a diverse and dynamic group of professionals from different countries working together.</p>
    <a class="btn" href="#">Learn More</a>
  </div>
</section>

<section class="benefits">
  <span class="eyebrow">Why choose us</span>
  <h2>EXTRA BENEFITS FOR PEOPLE</h2>
  <span class="arrow" style="left:30px"><svg width="14" height="14" viewBox="0 0 14 14"><path d="M9 2L4 7l5 5" stroke="#fff" stroke-width="2" fill="none"/></svg></span>
  <span class="arrow" style="right:30px"><svg width="14" height="14" viewBox="0 0 14 14"><path d="M5 2l5 5-5 5" stroke="#fff" stroke-width="2" fill="none"/></svg></span>
  <div class="cards">
    <div class="card"><div class="card-photo" style="background:linear-gradient(135deg,#333,#8c8c8c)" role="img" aria-label="Hands holding a loyalty card"></div><h4>Loyalty card with discounts on different locally facilities</h4></div>
    <div class="card"><div class="card-photo" style="background:linear-gradient(135deg,#d8d8d8,#838383)" role="img" aria-label="Signing a health insurance form"></div><h4>Health insurance and medical services reimbursed</h4></div>
    <div class="card"><div class="card-photo" style="background:linear-gradient(135deg,#4a4a4a,#b8b8b8)" role="img" aria-label="Legal advisor in an office"></div><h4>Lawyer for employee's legal services</h4></div>
    <div class="card"><div class="card-photo" style="background:linear-gradient(135deg,#9a9a9a,#3a3a3a)" role="img" aria-label="Transport bus on a city street"></div><h4>Paid transportation for employees, in very good conditions</h4></div>
  </div>
</section>

<section class="community">
  <div class="eyebrow">Join with us</div>
  <h2>VELMORA COMMUNITY ACTIVITIES</h2>
  <p>Ut enim ad minima veniam, quis nostrum exercitationem ullam corporis suscipit laboriosam, nisi ut aliquid ex ea commodi consequatur? Quis autem vel eum iure reprehenderit qui in ea voluptate velit esse quam nihil molestiae consequatur, vel illum qui dolorem eum fugiat quo voluptas nulla pariatur?</p>
  <a class="btn" href="#">Read More</a>
  <div class="media">
    <div class="media-left" role="img" aria-label="Team group in matching shirts at a community event"></div>
    <div class="media-right" role="img" aria-label="Aerial view of the factory site">
      <svg class="play" width="44" height="32" viewBox="0 0 44 32"><rect width="44" height="32" rx="8" fill="#1c1c1c"/><path d="M18 10l10 6-10 6z" fill="#fff"/></svg>
    </div>
  </div>
</section>

<section class="newsletter">
  <h2>SIGN UP FOR OUR NEWSLETTER</h2>
  <p>Subscribe so you don't miss out on our special promotions, just for our subscribed customers!</p>
  <div class="signup"><div class="field">Email Address</div><a class="btn" href="#">Subscribe Now</a></div>
</section>

<footer class="site-footer">
  <div class="f-about">
    <h3>ABOUT US</h3>
    <p>Quality garments crafted with care in Romania. We partner with fashion houses to deliver tailored production, on time and with precision.</p>
    <div class="socials"><span></span><span></span><span></span></div>
  </div>
  <div class="f-links">
    <h3>QUICK LINKS</h3>
    <ul><li>Home</li><li>About Us</li><li>Mission Vision</li><li>Benefits</li><li>Our Values</li></ul>
  </div>
  <div class="f-links">
    <h3>USEFUL LINKS</h3>
    <ul><li>Terms &amp; Conditions</li><li>Privacy Policy</li><li>Contact</li><li>Refund and Return</li><li>Retrieve Order</li></ul>
  </div>
  <div class="f-contact">
    <h3>CONTACT US</h3>
    <p>Str. Lalelelor 8, Oradea<br>Zip code 410001<br>Phone: +40 259 000 111<br>Fax: +40 259 000 112<br>Email: info@velmorafashion.ro</p>
  </div>
</footer>

</body>
</html>
```